KRV Photography Business Card Design

I would like a business card designed in the shape of a camera.
Would like to see various camera designs. Would like to see what the card looks like in different colors. Would like to see which logo looks better on the various camera designs so please show me some with the white logo and some with the black logo. If you need a different file formats please let me know.
Project Deadline Extended Reason: My grandfather passed away and dealing with funeral plans so need to extend deadline. Added Tuesday, March 1, 2016
Project Deadline Extended
Reason: I just got back from out of town. My grandfather's passing was the primary focus for me these past few weeks and the funeral is over so now I will concentrate on picking my business card design. I really appreciate each designer who has taken the time to submit a design. Your effort has not gone unnoticed. I look forward to seeing more amazing designs.
Business
Contact Information for Business Card
Dorine
555-418-2706
https://www.facebook.com/krvphotographyfreelance/
MonaDorine@krv-photography.example

```html
<!DOCTYPE html>
<html lang="en">
<head>
<meta charset="utf-8">
<title>KRV Photography – Business Cards</title>
<link rel="stylesheet" href="https://fonts.googleapis.com/css2?family=Open+Sans:wght@400;600;700&display=swap">
<style>
  :root {
    --backdrop: #bcbdbf;
    --card-black: #000000;
    --gold: #c58132;
    --gold-logo: #c9962f;
    --white: #ffffff;
    --rule-gray: #8a8a8a;
  }
  html, body {
    margin: 0;
    padding: 0;
    width: 1200px;
    height: 927px;
    overflow: hidden;
    background: var(--backdrop);
    font-family: "Open Sans", Arial, sans-serif;
  }
  .stage { position: relative; width: 1200px; height: 927px; }
  .card {
    position: absolute;
    top: 265px;
    width: 578px;
    height: 428px;
    transform: scale(0.927);
    transform-origin: top left;
  }
  .card--gold { left: 43.6px; --accent: var(--gold); --rule: #7a5420; }
  .card--white { left: 621px; --accent: var(--white); --rule: var(--rule-gray); }
  .card__shape {
    position: absolute; inset: 0;
    width: 578px; height: 428px;
    filter: drop-shadow(4px 6px 6px rgba(0,0,0,0.45));
  }
  .brand {
    position: absolute;
    right: 30px;
    top: 62px;
    display: flex;
    flex-direction: column;
    align-items: center;
  }
  .brand__dot {
    width: 88px; height: 88px;
    border-radius: 50%;
    background: var(--gold-logo);
    margin-left: 10px;
  }
  .brand__name {
    margin-top: 10px;
    color: var(--gold-logo);
    font-weight: 400;
    font-size: 25px;
    letter-spacing: 0.5px;
    white-space: nowrap;
  }
  .holder {
    position: absolute;
    left: 25px;
    top: 302px;
    right: 0;
    display: flex;
    align-items: center;
  }
  .holder__name {
    margin: 0;
    font-size: 26px;
    font-weight: 700;
    letter-spacing: 2.5px;
    color: var(--accent);
    white-space: nowrap;
  }
  .holder__rule {
    flex: 1;
    height: 1.5px;
    background: var(--rule);
    margin-left: 3px;
    margin-top: 6px;
  }
  .contact {
    position: absolute;
    left: 52px;
    top: 345px;
    margin: 0; padding: 0;
    list-style: none;
    color: var(--accent);
    font-size: 16px;
    letter-spacing: 1px;
    line-height: 20px;
  }
  .contact li { position: relative; }
  .contact__icon {
    position: absolute;
    left: -28px; top: 4px;
    width: 13px; height: 13px;
  }
</style>
</head>
<body>
<main class="stage">

  <section class="card card--gold" aria-label="Business card, gold version">
    <svg class="card__shape" viewBox="0 0 578 428" aria-hidden="true">
      <defs>
        <clipPath id="body-gold">
          <rect x="0" y="26" width="578" height="400" rx="22"/>
        </clipPath>
      </defs>
      <rect x="75" y="20" width="68" height="16" rx="6" fill="var(--card-black)"/>
      <rect x="406" y="1" width="112" height="40" rx="10" fill="var(--card-black)"/>
      <rect x="0" y="26" width="578" height="400" rx="22" fill="var(--card-black)"/>
      <path clip-path="url(#body-gold)" fill="var(--gold)"
            d="M0 406 H330 C340 392 352 386 372 386 H578 V428 H0 Z"/>
    </svg>
    <div class="brand">
      <span class="brand__dot"></span>
      <span class="brand__name">KRV PHOTOGRAPHY</span>
    </div>
    <div class="holder">
      <h2 class="holder__name">THEO MARSH</h2>
      <span class="holder__rule"></span>
    </div>
    <ul class="contact">
      <li>
        <svg class="contact__icon" viewBox="0 0 16 16" aria-hidden="true">
          <path d="M4 1 L6.5 4.5 L5 6.5 C6 9 7.5 10.5 9.5 11 L11.5 9.5 L15 12 L13 15 C7 14.5 1.5 9 1 3 Z" fill="none" stroke="var(--gold)" stroke-width="1.5" stroke-linejoin="round"/>
        </svg>
        +330 5550-1427
      </li>
      <li>
        <svg class="contact__icon" viewBox="0 0 16 16" aria-hidden="true">
          <rect x="1" y="3.5" width="14" height="10" fill="none" stroke="var(--gold)" stroke-width="1.5"/>
          <path d="M1 3.5 L8 9 L15 3.5" fill="none" stroke="var(--gold)" stroke-width="1.5"/>
        </svg>
        theo@marshmail.example
      </li>
    </ul>
  </section>

  <section class="card card--white" aria-label="Business card, white version">
    <svg class="card__shape" viewBox="0 0 578 428" aria-hidden="true">
      <defs>
        <clipPath id="body-white">
          <rect x="0" y="26" width="578" height="400" rx="22"/>
        </clipPath>
      </defs>
      <rect x="75" y="20" width="68" height="16" rx="6" fill="var(--card-black)"/>
      <rect x="406" y="1" width="112" height="40" rx="10" fill="var(--card-black)"/>
      <rect x="0" y="26" width="578" height="400" rx="22" fill="var(--card-black)"/>
      <path clip-path="url(#body-white)" fill="var(--white)"
            d="M0 406 H330 C340 392 352 386 372 386 H578 V428 H0 Z"/>
    </svg>
    <div class="brand">
      <span class="brand__dot"></span>
      <span class="brand__name">KRV PHOTOGRAPHY</span>
    </div>
    <div class="holder">
      <h2 class="holder__name">THEO MARSH</h2>
      <span class="holder__rule"></span>
    </div>
    <ul class="contact">
      <li>+330 5550-1427</li>
      <li>theo@marshmail.example</li>
    </ul>
  </section>

</main>
</body>
</html>
```